Tech business card design

We need an amazing business card design for our new business 'Pexla' a marketing tech startup based in Sydney, Australia. We provide an online marketplace for businesses to search and buy advertising media, connect with service providers and learn more about marketing. We wish to communicate 'cool tech', reliability and professionalism and design based around our logo.

Target Market(s)

Business Owners

Contact Information for Business Card

Name
Position
Email Address
Website
Phone Number

Font styles to use
Other font styles liked:
• Avenir & Avenir Next

Colors

Designer to choose colors to be used in the design.

```html
<!DOCTYPE html>
<html lang="en">
<head>
<meta charset="utf-8">
<title>Pexla Business Card</title>
<link rel="stylesheet" href="https://fonts.googleapis.com/css2?family=Nunito+Sans:wght@400;600;800;900&display=swap">
<style>
  :root {
    --navy: #0f1d4f;
    --navy-soft: #1a2c6e;
    --navy-deep: #0b1640;
    --white: #ffffff;
    --stage: #e4e5e7;
    --muted: #5f6470;
    --tm: #2a2f3a;
  }
  html, body {
    margin: 0;
    width: 1200px;
    height: 900px;
    overflow: hidden;
    background: var(--stage);
    font-family: "Nunito Sans", sans-serif;
  }
  .canvas {
    position: relative;
    width: 1200px;
    height: 900px;
  }
  .card {
    position: absolute;
    width: 560px;
    height: 320px;
    box-shadow: 0 10px 24px rgba(0, 0, 0, 0.25);
    overflow: hidden;
  }
  .card-back {
    left: 110px;
    top: 90px;
    background: var(--navy);
  }
  .card-front {
    left: 530px;
    top: 490px;
    background: var(--white);
  }
  .icon-pattern {
    position: absolute;
    inset: 0;
    background:
      linear-gradient(160deg, var(--navy-soft) 0%, var(--navy) 45%, var(--navy-deep) 100%);
  }
  .wordmark {
    position: absolute;
    font-weight: 900;
    letter-spacing: -1px;
    line-height: 1;
    white-space: nowrap;
  }
  .wordmark .tm {
    font-size: 11px;
    font-weight: 900;
    letter-spacing: 0;
    vertical-align: 0.9em;
    margin-left: 6px;
  }
  .card-back .wordmark {
    left: 40px;
    bottom: 44px;
    font-size: 72px;
    color: var(--white);
  }
  .card-back .wordmark .tm { color: var(--white); }
  .card-front .wordmark {
    left: 40px;
    bottom: 44px;
    font-size: 88px;
    color: var(--navy);
  }
  .card-front .wordmark .tm { color: var(--tm); }
  .contact-list {
    position: absolute;
    left: 330px;
    top: 150px;
    margin: 0;
    padding: 0;
    list-style: none;
    color: var(--white);
    font-size: 14px;
    font-weight: 400;
  }
  .contact-list li {
    display: flex;
    align-items: center;
    gap: 10px;
    height: 22px;
  }
  .contact-list svg {
    width: 13px;
    height: 13px;
    fill: none;
    stroke: var(--white);
    stroke-width: 1.6;
  }
  .person {
    position: absolute;
    left: 350px;
    top: 118px;
  }
  .person-name {
    margin: 0;
    color: var(--navy);
    font-size: 19px;
    font-weight: 800;
    letter-spacing: 0.5px;
    text-transform: uppercase;
  }
  .person-role {
    margin: 2px 0 0 14px;
    color: var(--muted);
    font-size: 14px;
    font-weight: 400;
  }
</style>
</head>
<body>
<main class="canvas">
  <section class="card card-back">
    <div class="icon-pattern" role="img" aria-label="Faint background pattern of marketing, finance and analytics line icons"></div>
    <div class="wordmark">pexla<span class="tm">TM</span></div>
    <ul class="contact-list">
      <li>
        <svg viewBox="0 0 16 16"><path d="M3 2h3l1.5 4-2 1.2a8 8 0 0 0 3.3 3.3L10 8.5l4 1.5v3a1 1 0 0 1-1 1A12 12 0 0 1 2 3a1 1 0 0 1 1-1z"/></svg>
        <span>000-555-0198</span>
      </li>
      <li>
        <svg viewBox="0 0 16 16"><rect x="1.5" y="3.5" width="13" height="9"/><path d="M1.5 3.5 8 9l6.5-5.5"/></svg>
        <span>info@pexlamail.com</span>
      </li>
      <li>
        <svg viewBox="0 0 16 16"><circle cx="8" cy="8" r="6.5"/><ellipse cx="8" cy="8" rx="3" ry="6.5"/><path d="M1.5 8h13"/></svg>
        <span>www.pexlamail.com</span>
      </li>
    </ul>
  </section>

  <section class="card card-front">
    <div class="person">
      <h1 class="person-name">Marcus Lane</h1>
      <p class="person-role">Managing Director</p>
    </div>
    <div class="wordmark">pexla<span class="tm">TM</span></div>
  </section>
</main>
</body>
</html>
```